Business card for a Exhibition booth fabrication company

Hi. My company would like to change our corporate name card. We are an events and Exhibition stand builder company. We would like our corporate name card to resonate what we do. I need someone to create something unique that relates to the industry that I am in. The graphic designer should be creative to incorporate the elements of my industry and try to blend in well in the design of the card. Our aim is to ensure that we are unique and our card can look different from our competitors.
Updates

Target Market(s)

Marketing and events manager from all companies

Contact Information for Business Card

The business card should have the following details:
Name
Job Title
Email
Website

Colors

Designer to choose colors to be used in the design.

Requirements
Must have
• The card must be look something that is relevant to the service that I am providing. My website is: www.velmora-buildworks.com
• You can see my website to get more information on what service that I am doing
Nice to have
• On the back of my card, I would like to have a globe image with the incorporation of my company logo. This is to indicate that my services can be done in any part of the world.

```html
<!DOCTYPE html>
<html lang="en">
<head>
<meta charset="utf-8">
<title>Velmora Buildworks – Business Card</title>
<link rel="stylesheet" href="https://fonts.googleapis.com/css2?family=Arimo:wght@400;700&family=Open+Sans:wght@400;600&display=swap">
<style>
  :root {
    --backdrop: #1f1f21;
    --card: #ffffff;
    --brand-red: #e41d26;
    --brand-grey: #6b6b6b;
    --swoosh-grey: #58585a;
    --text-grey: #555557;
    --map-light: #f2f2f2;
    --map-mid: #c9c9c9;
    --white: #ffffff;
  }
  * { box-sizing: border-box; margin: 0; padding: 0; }
  html, body {
    width: 1200px; height: 960px; overflow: hidden;
    background: var(--backdrop);
  }
  .canvas {
    position: relative; width: 1200px; height: 960px;
    background: var(--backdrop);
  }
  .card {
    position: absolute; width: 600px; height: 343px;
    background: var(--card); overflow: hidden;
    left: 300px;
  }
  .card--back { top: 90px; }
  .card--front { top: 527px; }

  /* Back */
  .globe-area {
    position: absolute; left: 150px; top: 14px; width: 420px; height: 190px;
    border-radius: 50% 50% 40% 40% / 60% 60% 40% 40%;
    background: radial-gradient(ellipse at 55% 45%, var(--map-mid) 0%, #dcdcdc 45%, var(--map-light) 75%, rgba(255,255,255,0) 100%);
  }
  .back-logo {
    position: absolute; left: 0; right: 0; top: 218px;
    display: flex; align-items: center; justify-content: center; gap: 14px;
  }
  .brand-mark {
    width: 22px; height: 22px; border-radius: 50%; background: var(--brand-red);
  }
  .brand-name {
    font-family: "Arimo", Arial, sans-serif; font-weight: 700;
    color: var(--brand-grey); letter-spacing: 3px; text-transform: uppercase;
  }
  .back-logo .brand-name { font-size: 26px; }

  /* Front */
  .front-logo {
    position: absolute; left: 70px; top: 34px;
    display: flex; align-items: center; gap: 10px;
  }
  .front-logo .brand-name { font-size: 20px; }
  .holder {
    position: absolute; left: 38px; top: 96px;
    font-family: "Arimo", Arial, sans-serif;
  }
  .holder__name { color: var(--brand-red); font-weight: 700; font-size: 17px; letter-spacing: 0.5px; }
  .holder__title { color: var(--text-grey); font-size: 12px; letter-spacing: 0.5px; margin-top: 2px; }
  .holder__address {
    margin-top: 10px; font-family: "Open Sans", Arial, sans-serif;
    color: var(--text-grey); font-size: 12px; line-height: 1.45;
  }
  .waves { position: absolute; left: 0; top: 0; width: 600px; height: 343px; }
  .contact {
    position: absolute; right: 22px; top: 262px;
    font-family: "Open Sans", Arial, sans-serif; font-size: 13px;
    color: var(--white); list-style: none; text-align: right;
  }
  .contact li { display: flex; align-items: center; justify-content: flex-end; gap: 10px; height: 23px; }
  .contact svg { width: 13px; height: 13px; flex: none; }
</style>
</head>
<body>
<main class="canvas">

  <section class="card card--back" aria-label="Card back">
    <div class="globe-area" role="img" aria-label="Soft grey world map suggesting global reach"></div>
    <div class="back-logo">
      <span class="brand-mark"></span>
      <span class="brand-name">Velmora Buildworks</span>
    </div>
  </section>

  <section class="card card--front" aria-label="Card front">
    <svg class="waves" viewBox="0 0 600 343" aria-hidden="true">
      <path d="M0,194 C150,202 300,250 600,228 L600,236 C300,258 150,214 0,210 Z" fill="var(--swoosh-grey)"/>
      <path d="M0,214 C150,220 300,262 600,240" fill="none" stroke="var(--swoosh-grey)" stroke-width="1.5"/>
      <path d="M0,224 C150,232 300,272 600,246 L600,343 L0,343 Z" fill="var(--brand-red)"/>
    </svg>

    <div class="front-logo">
      <span class="brand-mark"></span>
      <span class="brand-name">Velmora Buildworks</span>
    </div>

    <div class="holder">
      <p class="holder__name">DANIEL HARROW</p>
      <p class="holder__title">PRESIDENT</p>
      <p class="holder__address">Street Name, City Name<br>Zipcode - 01234</p>
    </div>

    <ul class="contact">
      <li>012-555-0142
        <svg viewBox="0 0 16 16"><path d="M3.5 1 L6 1 L7 5 L5.3 6.3 C6.2 8.2 7.8 9.8 9.7 10.7 L11 9 L15 10 L15 12.5 C15 14 13.8 15 12.3 15 C6.4 14.6 1.4 9.6 1 3.7 C1 2.2 2 1 3.5 1 Z" fill="var(--white)"/></svg>
      </li>
      <li>info@velmora-buildworks.com
        <svg viewBox="0 0 16 16"><rect x="1" y="3" width="14" height="10" fill="none" stroke="var(--white)" stroke-width="1.5"/><path d="M1 3 L8 9 L15 3" fill="none" stroke="var(--white)" stroke-width="1.5"/></svg>
      </li>
      <li>www.velmora-buildworks.com
        <svg viewBox="0 0 16 16"><circle cx="8" cy="8" r="6.5" fill="none" stroke="var(--white)" stroke-width="1.3"/><ellipse cx="8" cy="8" rx="3" ry="6.5" fill="none" stroke="var(--white)" stroke-width="1.1"/><path d="M1.5 8 H14.5 M2.5 5 H13.5 M2.5 11 H13.5" stroke="var(--white)" stroke-width="1"/></svg>
      </li>
    </ul>
  </section>

</main>
</body>
</html>
```